Floor Inspections and Consulting

We provide inspections and consulting services on various floor coverings, e.g. carpet, hardwood, etc. We also do expert witness work for attorneys due to floor covering failures. We current have a logo, just need it incorporated into a new design. I have examples of cards I have found on the internet that capture my attention and make a statement. I have included our original business card, which in my opinion is terrible, but it does have our logo on it.

```html
<!DOCTYPE html>
<html lang="en">
<head>
<meta charset="utf-8">
<title>Northfield Floor Inspections – Business Card</title>
<link rel="stylesheet" href="https://fonts.googleapis.com/css2?family=Montserrat:wght@600&family=Open+Sans:wght@300;400;700&display=swap">
<style>
  :root {
    --page-bg: #c9c9c9;
    --card-black: #020202;
    --gold: #c4a65f;
    --gold-light: #d6bd7f;
    --gold-deep: #b8984f;
    --white: #ffffff;
    --text-soft: #e6e6e6;
    --silver-dark: #6f6f6f;
    --silver-light: #f2f2f2;
    --back-glow: #3a3428;
  }
  * { margin: 0; padding: 0; box-sizing: border-box; }
  html, body { width: 1200px; height: 1200px; overflow: hidden; }
  body {
    background: var(--page-bg);
    font-family: "Open Sans", Arial, sans-serif;
    position: relative;
  }
  .card {
    position: absolute;
    left: 232px;
    width: 736px;
    height: 423px;
    border-radius: 40px;
    overflow: hidden;
  }
  .card-front { top: 106px; background: var(--card-black); }
  .card-back { top: 662px; }

  .front-shapes { position: absolute; inset: 0; width: 100%; height: 100%; }

  .tagline {
    position: absolute;
    left: 69px; top: 80px;
    color: var(--white);
    font-weight: 700;
    font-size: 18px;
    line-height: 22px;
  }
  .rule {
    position: absolute;
    left: 69px; top: 184px;
    width: 38px; height: 3px;
    background: var(--gold);
  }
  .person-name {
    position: absolute;
    left: 69px; top: 200px;
    color: var(--gold);
    font-family: "Montserrat", Arial, sans-serif;
    font-weight: 600;
    font-size: 22px;
    letter-spacing: 0.5px;
    text-transform: uppercase;
  }
  .person-role {
    position: absolute;
    left: 69px; top: 228px;
    color: var(--text-soft);
    font-weight: 300;
    font-size: 16px;
  }
  .contact-list {
    position: absolute;
    left: 69px; top: 276px;
    list-style: none;
    color: var(--text-soft);
    font-weight: 300;
    font-size: 17px;
    line-height: 21px;
  }
  .contact-list li { display: flex; align-items: center; gap: 11px; }
  .contact-list svg { width: 15px; height: 15px; flex: none; }

  .brand {
    position: absolute;
    display: flex;
    flex-direction: column;
    align-items: center;
    gap: 10px;
    text-align: center;
    font-family: "Open Sans", Arial, sans-serif;
    font-weight: 700;
    text-transform: uppercase;
    letter-spacing: 1px;
  }
  .brand-front {
    left: 460px; top: 150px; width: 224px;
    color: var(--white);
    font-size: 19px; line-height: 24px;
  }
  .brand-front .brand-dot { width: 18px; height: 18px; border-radius: 50%; background: var(--white); }
  .brand-back {
    left: 218px; top: 150px; width: 300px;
    color: var(--gold);
    font-size: 24px; line-height: 30px;
  }
  .brand-back .brand-dot { width: 22px; height: 22px; border-radius: 50%; background: var(--gold); }

  .back-fill {
    position: absolute; inset: 0;
    background: radial-gradient(circle at 50% 56%, var(--back-glow) 0%, #1b1914 45%, var(--card-black) 100%);
  }
</style>
</head>
<body>

<section class="card card-front">
  <svg class="front-shapes" viewBox="0 0 736 423" preserveAspectRatio="none" aria-hidden="true">
    <defs>
      <linearGradient id="silverEdge" x1="0" y1="0" x2="1" y2="1">
        <stop offset="0" stop-color="#8a8a8a"/>
        <stop offset="0.35" stop-color="#f4f4f4"/>
        <stop offset="0.7" stop-color="#7a7a7a"/>
        <stop offset="1" stop-color="#d8d8d8"/>
      </linearGradient>
      <radialGradient id="goldPanel" cx="0.72" cy="0.5" r="0.6">
        <stop offset="0" stop-color="#d8c08a"/>
        <stop offset="1" stop-color="#c09f55"/>
      </radialGradient>
    </defs>
    <g role="img" aria-label="Gold panel with radiating sunburst background">
      <path d="M 340 0 H 736 V 423 H 344 Q 512 211 340 0 Z" fill="url(#goldPanel)"/>
    </g>
    <path d="M 300 0 Q 500 211 340 423 L 344 423 Q 516 211 340 0 Z" fill="url(#silverEdge)"/>
    <path d="M 300 0 H 340 Q 516 211 344 423 H 338 Q 496 211 300 0 Z" fill="url(#silverEdge)"/>
  </svg>

  <p class="tagline">Certified Floor Covering<br>Inspections &amp; Consulting</p>
  <div class="rule"></div>
  <h1 class="person-name">Daniel Marbrook</h1>
  <p class="person-role">President</p>

  <ul class="contact-list">
    <li>
      <svg viewBox="0 0 16 16"><path fill="var(--gold)" d="M3.5 1.5l2.5 2.7-1.4 1.8c.8 1.8 2.3 3.3 4.1 4.1l1.8-1.4 2.7 2.5-1.5 2.3C6.6 13.6 2.4 9.4 1.5 3z"/></svg>
      <span>303-555-0148</span>
    </li>
    <li>
      <svg viewBox="0 0 16 16"><rect x="1" y="3.5" width="14" height="9" fill="var(--gold)"/><path d="M1.5 4l6.5 5 6.5-5" fill="none" stroke="#000" stroke-width="1.2"/></svg>
      <span>dan@northfieldfloor.com</span>
    </li>
    <li>
      <svg viewBox="0 0 16 16" fill="none" stroke="var(--gold)" stroke-width="1.3"><circle cx="8" cy="8" r="6.5"/><ellipse cx="8" cy="8" rx="2.8" ry="6.5"/><path d="M1.5 8h13M2.5 4.8h11M2.5 11.2h11"/></svg>
      <span>www.northfieldfloor.com</span>
    </li>
  </ul>

  <div class="brand brand-front">
    <span class="brand-dot"></span>
    <span>Northfield Floor<br>Inspections</span>
  </div>
</section>

<section class="card card-back">
  <div class="back-fill" role="img" aria-label="Dark background with radiating sunburst rays"></div>
  <div class="brand brand-back">
    <span class="brand-dot"></span>
    <span>Northfield Floor<br>Inspections</span>
  </div>
</section>

</body>
</html>
```